business card

Business card for new business.
Red and black corporate colors.
Card can have an Indsutrial feel to it. Feel free to add Rust, Bolted steel, or graphics as you see fit. We provide highly specialized services to the below mentioned industries.
Keep information out of corners so that if I want I can choose rounded corners.
Information
- front. name - title - phone - email
- Rear
Refining - Rail - Infrastructure - Mining - Energy
Calgary - Edmonton - Fort McMurray - Revelstoke - Vancouver

```html
<!DOCTYPE html>
<html lang="en">
<head>
<meta charset="utf-8">
<title>Keystrand Business Card</title>
<link href="https://fonts.googleapis.com/css2?family=Lato:wght@400;700;900&display=swap" rel="stylesheet">
<style>
  :root {
    --stage-top: #3a3a3a;
    --stage-bottom: #1e1e1e;
    --card-black: #020202;
    --brand-red: #e0202a;
    --brand-grey: #8b8889;
    --ink-white: #f4f4f4;
    --rule: #d9d9d9;
  }
  * { margin: 0; padding: 0; box-sizing: border-box; }
  html, body { width: 1200px; height: 1200px; overflow: hidden; }
  body {
    background: radial-gradient(ellipse at 50% 40%, var(--stage-top), var(--stage-bottom));
    font-family: "Lato", Arial, sans-serif;
    color: var(--ink-white);
    position: relative;
  }
  .card {
    position: absolute;
    left: 120px;
    width: 960px;
    height: 548px;
    background: var(--card-black);
    box-shadow: 0 14px 30px rgba(0,0,0,.5);
  }
  .card--back { top: 28px; }
  .card--front { top: 624px; }

  .wordmark {
    position: absolute;
    display: flex;
    align-items: center;
    gap: 18px;
    font-weight: 900;
    color: var(--brand-grey);
    text-transform: uppercase;
    letter-spacing: 2px;
    line-height: 1;
  }
  .wordmark__square {
    width: 26px; height: 26px;
    background: var(--brand-red);
    flex: none;
  }
  .card--back .wordmark {
    left: 0; right: 0; top: 160px;
    justify-content: center;
    font-size: 104px;
  }
  .card--front .wordmark {
    right: 70px; top: 60px;
    font-size: 80px;
  }

  .service-list {
    position: absolute;
    left: 0; right: 0; top: 380px;
    text-align: center;
    font-size: 26px;
    line-height: 38px;
    letter-spacing: .3px;
  }
  .service-list .dot {
    display: inline-block;
    width: 7px; height: 7px;
    border-radius: 50%;
    background: var(--brand-red);
    margin: 0 10px;
    vertical-align: middle;
  }

  .holder {
    position: absolute;
    left: 70px; top: 218px;
  }
  .holder__name {
    color: var(--brand-red);
    font-weight: 700;
    font-size: 36px;
  }
  .holder__title {
    font-size: 25px;
    margin-top: 4px;
  }
  .divider {
    position: absolute;
    left: 70px; right: 70px; top: 318px;
    height: 2px;
    background: var(--rule);
  }
  .contact-list {
    position: absolute;
    left: 70px; top: 352px;
    list-style: none;
    font-size: 26px;
  }
  .contact-list li {
    display: flex;
    align-items: center;
    gap: 22px;
    height: 40px;
  }
  .contact-list svg { width: 22px; height: 22px; fill: var(--brand-red); flex: none; }
  .address {
    position: absolute;
    right: 70px; top: 344px;
    text-align: right;
    font-size: 26px;
    line-height: 34px;
  }
  .base-band {
    position: absolute;
    left: 0; right: 0; bottom: 0;
    height: 14px;
    background: var(--brand-red);
  }
</style>
</head>
<body>

<section class="card card--back" aria-label="Card reverse">
  <div class="wordmark"><span class="wordmark__square"></span>Keystrand</div>
  <p class="service-list">
    Refining<span class="dot"></span>Rail<span class="dot"></span>Infrastructure<span class="dot"></span>Mining<span class="dot"></span>Energy<br>
    Calgary<span class="dot"></span>Edmonton<span class="dot"></span>Fort McMurray<span class="dot"></span>Revelstoke<span class="dot"></span>Vancouver
  </p>
</section>

<section class="card card--front" aria-label="Card front">
  <div class="wordmark"><span class="wordmark__square"></span>Keystrand</div>

  <div class="holder">
    <p class="holder__name">Daniel Hartley</p>
    <p class="holder__title">Manager</p>
  </div>
  <div class="divider"></div>

  <ul class="contact-list">
    <li>
      <svg viewBox="0 0 24 24" aria-hidden="true"><path d="M6.6 10.8a15.1 15.1 0 0 0 6.6 6.6l2.2-2.2a1 1 0 0 1 1-.25 11.4 11.4 0 0 0 3.6.57 1 1 0 0 1 1 1V20a1 1 0 0 1-1 1A17 17 0 0 1 3 4a1 1 0 0 1 1-1h3.5a1 1 0 0 1 1 1c0 1.25.2 2.45.57 3.57a1 1 0 0 1-.25 1z"/></svg>
      512 555 0142
    </li>
    <li>
      <svg viewBox="0 0 24 24" aria-hidden="true"><path d="M2 5h20v14H2z M3.5 6.5 12 13l8.5-6.5" fill="none" stroke="#e0202a" stroke-width="2"/></svg>
      info@keystrand.com
    </li>
    <li>
      <svg viewBox="0 0 24 24" aria-hidden="true"><circle cx="12" cy="12" r="9" fill="none" stroke="#e0202a" stroke-width="2"/><path d="M3 12h18M12 3c-3 3.5-3 14.5 0 18M12 3c3 3.5 3 14.5 0 18" fill="none" stroke="#e0202a" stroke-width="1.6"/></svg>
      www.keystrand.com
    </li>
  </ul>

  <p class="address">418 Fenwick Lane<br>Houston, TX 77041</p>
  <div class="base-band"></div>
</section>

</body>
</html>
```